Maple Sprout Menu (Vegetarian Restaurant Concept)

Maple Sprout is a new concept fast casual restaurant
renders are attached so you can see the style of restaurant
Maple Sproute is a vibrant and modern Vegetarian fast casual restaurant concept that mixes fresh food, energy, great décor, and a comfortable, welcoming atmosphere to provide a memorable and all Vegetarian dining experience.
Our Mission is to be top of mind when consumers think Vegetarian food!
Updates
Need extra days to review
Target Market(s)
the menu is vegetarian and appeals to a broad demographic in USA
Font styles to use
Colors
Designer to choose colors to be used in the design.
Requirements
Must have
- well colored and well laid out menu - should not be cartoonish
Nice to have
- For Phots please use the shots in this file:
- https://www.filecrate-share.net/sh/qtrv8knw2lpa5zc/BBBxR_pLmNoQwEE4J_TKX_Va?dl=0
- note these are untouched and you are free to change as needed
Should not have
- Should not be cartoonish - nor kives, forks etc in the design

```html
<!DOCTYPE html>
<html lang="en">
<head>
<meta charset="utf-8">
<title>Maple Sproute Menu</title>
<link rel="stylesheet" href="https://fonts.googleapis.com/css2?family=Montserrat:wght@400;600;700;800;900&display=swap">
<style>
  :root {
    --ink: #000000;
    --paper: #ffffff;
    --leaf: #7ab929;
    --mist: #a9a9a9;
    --rule: #333333;
  }
  * { margin: 0; padding: 0; box-sizing: border-box; }
  html, body { width: 847px; height: 1200px; overflow: hidden; background: var(--ink); }
  .menu {
    position: relative; width: 847px; height: 1200px; overflow: hidden;
    background: var(--ink); color: var(--paper);
    font-family: "Montserrat", Arial, sans-serif;
  }
  .hero-photo {
    position: absolute; left: 0; top: 0; width: 847px; height: 360px;
    background:
      radial-gradient(circle at 600px 150px, #f2f1ec 0, #e6e4dc 150px, #4a4a48 215px, transparent 216px),
      linear-gradient(135deg, #2b2b2b 0%, #5a5a58 35%, #1a1a1a 70%, #000 100%);
  }
  .hero-fade {
    position: absolute; left: 0; top: 280px; width: 847px; height: 80px;
    background: linear-gradient(to bottom, rgba(0,0,0,0), var(--ink));
  }
  .brand {
    position: absolute; left: 30px; top: 110px; width: 160px;
    display: flex; flex-direction: column; align-items: center; gap: 10px;
  }
  .brand-dot { width: 58px; height: 58px; border-radius: 50%; background: var(--leaf); }
  .brand-name { font-weight: 800; font-size: 24px; color: var(--paper); text-align: center; line-height: 1.05; }
  .title-band {
    position: absolute; left: 368px; top: 118px; width: 456px; height: 150px;
    background: rgba(255,255,255,0.55);
    display: flex; align-items: center; justify-content: center;
  }
  .title {
    font-weight: 900; font-size: 112px; letter-spacing: 2px;
    color: var(--leaf); line-height: 1; white-space: nowrap;
  }
  .col { position: absolute; top: 430px; }
  .col-left { left: 28px; width: 390px; }
  .col-right { left: 443px; width: 380px; text-align: right; }
  .col-right .section-first .section-title { text-align: left; }
  .divider { position: absolute; left: 428px; top: 440px; width: 1px; height: 620px; background: var(--rule); }
  .section { margin-bottom: 34px; }
  .section-title {
    font-weight: 800; font-size: 19px; letter-spacing: 0.3px; white-space: nowrap;
    padding-bottom: 6px; border-bottom: 2px solid var(--leaf); margin-bottom: 14px;
  }
  .item { margin-bottom: 13px; }
  .item-name { font-weight: 700; font-size: 12.5px; text-transform: uppercase; letter-spacing: 0.1px; white-space: nowrap; }
  .item-desc { font-size: 10.5px; color: var(--mist); margin-top: 2px; line-height: 1.3; }
  .social { position: absolute; left: 36px; top: 1100px; display: flex; flex-direction: column; gap: 22px; }
  .social-mark { width: 26px; height: 26px; border-radius: 6px; background: var(--paper); }
  .enjoy-band {
    position: absolute; left: 425px; top: 1095px; width: 422px; height: 76px;
    background: var(--leaf); display: flex; align-items: center; justify-content: center;
  }
  .enjoy { font-weight: 900; font-size: 46px; letter-spacing: 3px; color: var(--paper); }
</style>
</head>
<body>
<main class="menu">
  <div class="hero-photo" role="img" aria-label="Photo of a fresh leafy salad in a white bowl on a checkered tablecloth"></div>
  <div class="hero-fade"></div>

  <div class="brand">
    <span class="brand-dot"></span>
    <span class="brand-name">Maple Sproute</span>
  </div>

  <div class="title-band"><h1 class="title">MENU</h1></div>

  <div class="divider"></div>

  <section class="col col-left">
    <div class="section">
      <h2 class="section-title">SALADS</h2>
      <div class="item"><p class="item-name">Brussel Sprout Caesar</p><p class="item-desc">little gem romaine, toasted corn bread, parmiggiano reggiano</p></div>
      <div class="item"><p class="item-name">Heirloom Beet Salad</p><p class="item-desc">shaved chioggia beet, roasted golden beet, red quinoa<br>little gem, arugula, lemon vinaigrette</p></div>
      <div class="item"><p class="item-name">Zesty Black Bean &amp; Corn Salad in Lettuce Cups</p><p class="item-desc">black beans, avocado and toasted corn topped with feta crumbles<br>in butter lettuce</p></div>
      <div class="item"><p class="item-name">Green, Red &amp; White</p><p class="item-desc">spring leaves, cherry tomatoes, avocado<br>roasted almond and goat cheese</p></div>
    </div>
    <div class="section">
      <h2 class="section-title">TOASTS</h2>
      <div class="item"><p class="item-name">Everything Avocado Toast</p><p class="item-desc">avocado on whole grain toast with our signature spice blend</p></div>
      <div class="item"><p class="item-name">Tomato &amp; Beet Bruschetta</p></div>
      <div class="item"><p class="item-name">Vegetable Melt on Garlic Toast</p></div>
    </div>
    <div class="section">
      <h2 class="section-title">SOUP</h2>
      <div class="item"><p class="item-name">Black Bean Chowder</p></div>
    </div>
  </section>

  <section class="col col-right">
    <div class="section section-first">
      <h2 class="section-title">BURGERS / WRAPS / SANDWICHES</h2>
      <div class="item"><p class="item-name">Sweet Potato, Black Bean Veggie Burger</p><p class="item-desc">with cabbage - pepita slaw</p></div>
      <div class="item"><p class="item-name">Roasted Veggie, Arugula and Hummus Wrap</p></div>
      <div class="item"><p class="item-name">Garden Burger</p></div>
      <div class="item"><p class="item-name">Beans &amp; Greens Quesadilla</p><p class="item-desc">greens, Mexican cheese, beans, avocado, salsa</p></div>
      <div class="item"><p class="item-name">Sproute Burrito</p><p class="item-desc">greens, Mexican cheese, beans, brown rice, toasted chili corn<br>avocado and hot chili salsa, wheat tortilla</p></div>
    </div>
    <div class="section">
      <h2 class="section-title">BOWLS</h2>
      <div class="item"><p class="item-name">Roasted Vegetable &amp; Spinach</p></div>
      <div class="item"><p class="item-name">Sugar Snap Pea &amp; Carrot Soba Noodles</p></div>
      <div class="item"><p class="item-name">Whole Grain and Vegetable Buddha</p></div>
      <div class="item"><p class="item-name">Orange &amp; Pistacio Quinoa</p></div>
    </div>
    <div class="section">
      <h2 class="section-title">DESSERTS</h2>
      <div class="item"><p class="item-name">Strawberry Balsamic Ice Cream Sundae</p></div>
      <div class="item"><p class="item-name">Exotic Fruit Bowl</p></div>
      <div class="item"><p class="item-name">White and Dark Oatmeal Cookie</p></div>
    </div>
  </section>

  <div class="social">
    <span class="social-mark"></span>
    <span class="social-mark"></span>
  </div>

  <div class="enjoy-band"><p class="enjoy">ENJOY!</p></div>
</main>
</body>
</html>
```